LM-Steuerberatung WordPress Site fully implemented (tax advisor)

Hello!
I need a little Wordpress Site for my newly founded Tax-Advisor Company.
I am a one-man Office advising in the area of Crypto-Currency.
PLEASE only provide a Design, if you can also Implement a WP-Site afterwards on an existing Webspace.

Please find the Content and Website-Description in the attached Document

Language for the Website is German (for now)

Target Market(s)

Tax-Advisory (specialized in Crypto Currency)

Coding

Coded - Design and coding required

Number of Pages Required

5+ page

Font styles to use
Sans Serif

Requirements
Must have
• Wordpress Implementation afterwards - Details according to attached Project Information Document

```html
<!DOCTYPE html>
<html lang="de">
<head>
<meta charset="utf-8">
<title>LM-Steuerberatung</title>
<link href="https://fonts.googleapis.com/css2?family=Poppins:ital,wght@0,400;0,500;0,600;0,700;0,800;1,500&display=swap" rel="stylesheet">
<style>
:root{
  --navy:#1c2b45;
  --text:#3a3f4a;
  --grey-btn:#a9a9a9;
  --band:#f4f4f4;
  --white:#ffffff;
}
*{margin:0;padding:0;box-sizing:border-box}
html,body{width:1183px;height:1200px;overflow:hidden;background:var(--white);font-family:'Poppins',sans-serif;color:var(--text)}
.page{position:relative;width:1183px;height:1200px}
.brand{position:absolute;display:flex;align-items:center;gap:12px;font-weight:600;font-size:21px;letter-spacing:.5px;color:var(--navy)}
.brand-mark{width:30px;height:30px;border-radius:50%;background:var(--navy)}
.site-header .brand{left:73px;top:38px}
.main-nav{position:absolute;top:47px;left:0;width:1183px;font-size:14px;font-weight:500;color:var(--text);letter-spacing:.3px}
.main-nav span{position:absolute;white-space:nowrap}
.main-nav .active{color:var(--navy);font-weight:600}
.hero{position:absolute;left:0;top:106px;width:1183px;height:634px;background:linear-gradient(160deg,#5f6b7d 0%,#414d61 45%,#2a3446 100%)}
.hero-title{position:absolute;left:0;top:172px;width:1183px;text-align:center;color:var(--white);font-weight:800;font-size:60px;line-height:66px;letter-spacing:.5px}
.hero-sub{position:absolute;left:0;top:314px;width:1183px;text-align:center;color:var(--white);font-weight:500;font-size:23px;line-height:37px}
.hero-btn{position:absolute;left:424px;top:407px;width:336px;height:49px;background:var(--grey-btn);color:var(--white);font-weight:700;font-size:16px;display:flex;align-items:center;justify-content:center;letter-spacing:.3px}
.quote-band{position:absolute;left:0;top:740px;width:1183px;height:171px;background:var(--band)}
.quote{position:absolute;left:0;top:52px;width:1183px;text-align:center;font-style:italic;font-weight:500;font-size:18px;line-height:31px;color:var(--navy);letter-spacing:.3px}
.arrow{position:absolute;top:72px}
.site-footer .brand{left:73px;top:972px}
.copyright{position:absolute;left:72px;top:1037px;font-size:15.5px;line-height:27px;color:var(--text)}
.footer-col{position:absolute;top:952px}
.footer-col h3{font-size:16px;font-weight:700;color:var(--navy);letter-spacing:.5px;margin-bottom:8px}
.footer-col li{list-style:none;font-size:16px;line-height:33.7px;color:var(--text)}
.contact-row{display:flex;align-items:center;gap:18px;font-size:16px;height:37px}
.contact-row strong{font-weight:600}
.social{display:flex;gap:26px;margin-top:14px}
.social span{width:24px;height:24px;border-radius:50%;background:var(--text)}
</style>
</head>
<body>
<div class="page">
  <header class="site-header">
    <div class="brand"><span class="brand-mark"></span>LM STEUERBERATUNG</div>
    <nav class="main-nav">
      <span class="active" style="left:578px">● HOME</span>
      <span style="left:682px">LEISTUNGEN ⌄</span>
      <span style="left:814px">ÜBER MICH</span>
      <span style="left:927px">KONTAKT</span>
      <span style="left:1030px">IMPRESSUM</span>
    </nav>
  </header>

  <section class="hero" role="img" aria-label="Foto: Berater im Büro mit Tablet vor Bildschirmen mit Kurscharts">
    <h1 class="hero-title">WILLKOMMEN BEI<br>LM-STEUERBERATUNG!</h1>
    <p class="hero-sub">Ihrem Spezialisten bei allen steuerlichen Themen rund um<br>Einkünfte Vermögen aus Krypto-Assets.</p>
    <div class="hero-btn">WEITER ZU UNSEREN LEISTUNGEN</div>
  </section>

  <section class="quote-band">
    <svg class="arrow" style="left:222px" width="16" height="28" viewBox="0 0 16 28"><path d="M14 2 2 14l12 12" fill="none" stroke="#1c2b45" stroke-width="2"/></svg>
    <p class="quote">“ Dann mach ich eine Schweizer Holding-Gesellschaft–<br>dort zahlt man fast keine Steuern..”</p>
    <svg class="arrow" style="left:945px" width="16" height="28" viewBox="0 0 16 28"><path d="M2 2l12 12L2 26" fill="none" stroke="#1c2b45" stroke-width="2"/></svg>
  </section>

  <footer class="site-footer">
    <div class="brand"><span class="brand-mark"></span>LM STEUERBERATUNG</div>
    <p class="copyright">2022 © Copyright Company Name.<br>All Rights Reserved</p>
    <div class="footer-col" style="left:428px">
      <h3>VERKNÜPFUNGEN</h3>
      <ul><li>Home</li><li>Leistungen</li><li>Über Mich</li><li>Kontakt</li><li>Impressum</li></ul>
    </div>
    <div class="footer-col" style="left:651px">
      <h3>LEISTUNGEN</h3>
      <ul><li>Neque porro</li><li>Quisquam est qui</li><li>Dolorem ipsum</li><li>Quia dolor</li></ul>
    </div>
    <div class="footer-col" style="left:872px">
      <h3>KONTAKT</h3>
      <div class="contact-row">
        <svg width="16" height="16" viewBox="0 0 24 24"><path d="M6 2h4l2 5-3 2a12 12 0 0 0 6 6l2-3 5 2v4a2 2 0 0 1-2 2A18 18 0 0 1 4 4a2 2 0 0 1 2-2z" fill="#1c2b45"/></svg>
        <strong>+43 512 400 218</strong>
      </div>
      <div class="contact-row">
        <svg width="17" height="13" viewBox="0 0 17 13"><rect width="17" height="13" rx="1" fill="#1c2b45"/><path d="M1 1l7.5 6L16 1" fill="none" stroke="#fff" stroke-width="1.4"/></svg>
        <span>kanzlei@lm-steuer.example</span>
      </div>
      <div class="social" aria-label="Soziale Netzwerke">
        <span></span><span></span><span></span><span></span><span></span>
      </div>
    </div>
  </footer>
</div>
</body>
</html>
```